Postcard for Real estate agent

**Scroll all the way down for updates***.....
I want a postcard to send out to potential clients to list their house on the market.
I submitting a a basic proof with the info and images that I want on each side of the postcard. I do not want a white postcard
-I want the postcard sized 6" x 4" inches
I want my phone number to stand out
I want a PLX and Homevane log on my postcard .Ive included examples of logos.
Feel free toe crop or enhance the images
Must look professional
-----------------------------------------------------------------------
UPDATE : August 4 , 2015 8pm Pacific Daylight Time , UTC -7
I submitted a proof of postcard I designed myself (see File 10)
Please use that for the front of the postcard.
For the back please refine the back to make it look professional
(see example of File 11 )
-----------------------------------------------------------------------------------------------------------
UPDATE: August 5 12:45 pm Pacific Daylight Time (UTC -7)
Please use Files 12, 13 and 14 on the front. No generic pictures.
You may crop and enhance my images if needed.
On the back, bottom of the postcard must have "If you are listed with another broker please disregard this mailing. This is not a solicitation"
UPDATE: August 5 12:45 pm Pacific Daylight Time (UTC -7)-------------------------------------------------------------------------------------Please use new Files 12, 13 and 14 on the front. No generic pictures.You may crop and enhance my images if needed.On the back, bottom of the postcard must have "If you are listed with another broker please disregard this mailing. This is not a solicitation"Upper left must have return address : 482 Corbel Rd #K Avalon CA 90815-6130 Added Wednesday, August 5, 2015
Homeowners wanting to sell their property
Real Estate Agent
- My name and phone number highly visible
- Homevane/ PLX logo
- Nothing pink, purple, lavender, brown , no pastels

```html
<!DOCTYPE html>
<html lang="en">
<head>
<meta charset="utf-8">
<title>Dana Whitcombe – Listing Postcard</title>
<link href="https://fonts.googleapis.com/css2?family=Cinzel:wght@700&family=Oswald:wght@400;500&family=Roboto+Condensed:wght@400;700&display=swap" rel="stylesheet">
<style>
  :root{
    --red:#e0262b;
    --charcoal:#2a2b2f;
    --charcoal-soft:#3b3d42;
    --white:#ffffff;
    --paper:#eeeeef;
    --ink:#222326;
    --stage:#d9dadc;
  }
  *{box-sizing:border-box;margin:0;padding:0}
  html,body{width:900px;height:1200px;overflow:hidden;background:var(--stage)}
  body{position:relative;font-family:"Roboto Condensed",sans-serif;color:var(--ink)}
  .postcard{position:absolute;left:30px;width:840px;height:560px;overflow:hidden;box-shadow:0 4px 14px rgba(0,0,0,.25)}
  .postcard--front{top:30px}
  .postcard--back{top:610px;background:linear-gradient(90deg,#e4e5e7 0%,#f7f7f8 50%,#ffffff 52%)}
  .layer{position:absolute;inset:0}
  .house-photo{position:absolute;inset:0;background:linear-gradient(160deg,#b9bdb6 0%,#7f8a74 40%,#4d6a3c 70%,#3a4a2e 100%)}
  .brand-row{position:absolute;top:22px;left:28px;display:flex;gap:18px;align-items:center}
  .brand{display:flex;align-items:center;gap:6px;font-family:"Oswald",sans-serif;font-weight:500;font-size:24px;line-height:1}
  .brand__mark{width:22px;height:22px}
  .brand--homevane{color:var(--charcoal)}
  .brand--homevane .brand__mark{background:var(--charcoal)}
  .brand--plx{color:var(--red)}
  .brand--plx .brand__mark{background:var(--red)}
  .photo-circle{position:absolute;border-radius:50%;border:5px solid var(--white);box-shadow:0 3px 8px rgba(0,0,0,.35)}
  .photo-circle--porch{left:92px;top:335px;width:130px;height:130px;background:linear-gradient(150deg,#8a7a62,#556b3b)}
  .photo-circle--sign{left:312px;top:238px;width:160px;height:160px;background:linear-gradient(150deg,#d8d6cf,#8c9a80)}
  .photo-circle--open-house{left:520px;top:150px;width:180px;height:180px;background:linear-gradient(150deg,#b3a99a,#5f6b55)}
  .pitch{position:absolute;left:486px;top:418px}
  .pitch__headline{font-family:"Cinzel",serif;font-weight:700;font-size:30px;color:var(--red);letter-spacing:.5px}
  .pitch__phone{font-family:"Oswald",sans-serif;font-size:28px;color:var(--white);margin-top:6px}
  .pitch__phone strong{font-weight:500;letter-spacing:1px}

  .agent-photo{position:absolute;left:30px;top:110px;width:150px;height:150px;border-radius:50%;border:6px solid var(--red);background:linear-gradient(160deg,#e7e3df,#b69a78);box-shadow:0 0 0 3px var(--white)}
  .agent-tag{position:absolute;left:150px;top:140px;width:232px;padding:10px 14px 10px 38px;background:var(--red);color:var(--white);z-index:-0}
  .agent-tag__name{font-weight:700;font-size:18px}
  .agent-tag__phone{font-weight:700;font-size:18px;margin-top:2px}
  .agent-tag__firm{font-size:14px;margin-top:6px;line-height:1.25}
  .disclaimer{position:absolute;left:30px;top:300px;width:360px;font-size:16px;line-height:1.35;color:var(--ink)}
  .return-address{position:absolute;left:30px;top:370px;font-family:"Oswald",sans-serif;font-size:18px;color:var(--red)}
  .contact-bar{position:absolute;left:0;bottom:0;width:420px;height:92px;background:var(--charcoal);padding:18px 0 0 30px;color:var(--white);font-size:14px}
  .contact-bar::after{content:"";position:absolute;right:-40px;top:0;border-left:40px solid var(--charcoal);border-top:92px solid transparent}
  .contact-line{display:flex;align-items:center;gap:8px;margin-bottom:10px}
  .contact-line svg{width:16px;height:16px}
  .stamp-box{position:absolute;right:60px;top:110px;width:88px;height:104px;border:3px solid var(--ink);background:var(--white)}
</style>
</head>
<body>

<section class="postcard postcard--front" aria-label="Postcard front">
  <div class="house-photo" role="img" aria-label="Photo of the agent's listed townhouse with garden"></div>
  <svg class="layer" viewBox="0 0 840 560" aria-hidden="true">
    <path d="M0,0 H520 C420,50 250,95 0,120 Z" fill="#ffffff"/>
    <path d="M520,0 H560 C450,60 270,110 0,138 V120 C250,95 420,50 520,0 Z" fill="#2a2b2f"/>
    <path d="M560,0 H576 C460,66 280,118 0,146 V138 C270,110 450,60 560,0 Z" fill="#e0262b"/>
    <path d="M0,412 C240,350 520,300 840,230 V560 H0 Z" fill="#e0262b"/>
    <path d="M0,428 C250,368 530,320 840,252 V560 H0 Z" fill="#2a2b2f"/>
  </svg>
  <div class="brand-row">
    <div class="brand brand--homevane"><span class="brand__mark"></span>Homevane</div>
    <div class="brand brand--plx"><span class="brand__mark"></span>PLX</div>
  </div>
  <div class="photo-circle photo-circle--porch" role="img" aria-label="Photo of the front patio and planters"></div>
  <div class="photo-circle photo-circle--sign" role="img" aria-label="Photo of the agent's for-sale sign in the yard"></div>
  <div class="photo-circle photo-circle--open-house" role="img" aria-label="Photo of an open house sign on the street"></div>
  <div class="pitch">
    <p class="pitch__headline">Thinking of selling?</p>
    <p class="pitch__phone">Call me today <strong>310 555 0184</strong></p>
  </div>
</section>

<section class="postcard postcard--back" aria-label="Postcard back">
  <svg class="layer" viewBox="0 0 840 560" aria-hidden="true">
    <rect x="0" y="0" width="840" height="74" fill="#ffffff"/>
    <path d="M250,0 H840 V78 C640,96 420,70 250,0 Z" fill="#2a2b2f"/>
    <path d="M250,0 C420,70 640,96 840,78 V86 C640,104 420,78 240,0 Z" fill="#e0262b"/>
  </svg>
  <div class="brand-row">
    <div class="brand brand--homevane"><span class="brand__mark"></span>Homevane</div>
    <div class="brand brand--plx"><span class="brand__mark"></span>PLX</div>
  </div>
  <div class="agent-tag">
    <p class="agent-tag__name">Dana Whitcombe</p>
    <p class="agent-tag__phone">Call (310) 555-0184</p>
    <p class="agent-tag__firm">Harborline Realtors<br>Wes Larkin, Broker</p>
  </div>
  <div class="agent-photo" role="img" aria-label="Portrait photo of the agent"></div>
  <p class="disclaimer">If you are listed with another broker please disregard this mailing. This is not a solicitation</p>
  <p class="return-address">482 Corbel Rd #K, Avalon, CA 90815-6130</p>
  <div class="contact-bar">
    <div class="contact-line">
      <svg viewBox="0 0 16 16"><circle cx="8" cy="8" r="8" fill="#ffffff"/><rect x="3.5" y="5" width="9" height="6" fill="none" stroke="#2a2b2f" stroke-width="1.2"/><path d="M3.5,5 L8,8.5 L12.5,5" fill="none" stroke="#2a2b2f" stroke-width="1.2"/></svg>
      <span>dana.whitcombe@mail.com</span>
    </div>
    <div class="contact-line">
      <svg viewBox="0 0 16 16"><circle cx="8" cy="8" r="8" fill="#ffffff"/><circle cx="8" cy="8" r="4.5" fill="none" stroke="#2a2b2f" stroke-width="1.2"/><path d="M3.5,8 H12.5 M8,3.5 V12.5" stroke="#2a2b2f" stroke-width="1"/></svg>
      <span>www.HarborlineRealtors.com</span>
    </div>
  </div>
  <div class="stamp-box" aria-label="Stamp area"></div>
</section>

</body>
</html>
```